IT Company requires new Business Card design.

Over the years we have had a few different business card designs. We are now due for new cards across the board for all staff. We felt this would be a good time to start fresh with a new design. Our traditional card simply had our details on the front, and a list of services on the back. We don't particularly need the list of services, we have had cards where the only thing on the rear of the card was our logo.
Feel free to be creative, we would like our tag line "Complete IT Management" to appear at some point, doesn't necessarily have to be with the logo.
I have attached samples and drafts of various previous cards we have used over the years.

```html
<!DOCTYPE html>
<html lang="en">
<head>
<meta charset="utf-8">
<title>Ridgeway Networking – Business Card</title>
<link rel="stylesheet" href="https://fonts.googleapis.com/css2?family=Open+Sans:wght@400;600;800&display=swap">
<style>
  :root {
    --bg: #e4e4ec;
    --card-dark-1: #1c1c1e;
    --card-dark-2: #3a3a3c;
    --card-dark-3: #2a2a2c;
    --blue: #2170a8;
    --blue-light: #3fa9e0;
    --silver: #b8b8bc;
    --white: #ffffff;
    --name-blue: #cfe6f7;
  }
  * { margin: 0; padding: 0; box-sizing: border-box; }
  html, body {
    width: 1200px; height: 987px; overflow: hidden;
    background: var(--bg);
    font-family: "Open Sans", Arial, sans-serif;
  }
  .canvas { position: relative; width: 1200px; height: 987px; }

  .card {
    position: absolute;
    width: 580px; height: 331px;
    border-radius: 22px;
    overflow: hidden;
    background:
      repeating-linear-gradient(100deg, rgba(255,255,255,0.03) 0 1px, transparent 1px 3px),
      linear-gradient(160deg, var(--card-dark-2) 0%, var(--card-dark-1) 45%, var(--card-dark-3) 100%);
    box-shadow: 0 14px 30px rgba(40,40,60,0.25);
    color: var(--white);
  }
  .card--back { left: 560px; top: 110px; }
  .card--front { left: 60px; top: 520px; }

  .wordmark {
    position: absolute;
    display: flex; align-items: center; gap: 16px;
  }
  .wordmark__mark {
    width: 58px; height: 58px;
    background: var(--silver);
  }
  .wordmark__name {
    font-weight: 800;
    font-size: 34px;
    line-height: 0.95;
    letter-spacing: 0.5px;
    color: var(--white);
    text-transform: uppercase;
  }
  .card--back .wordmark { left: 120px; top: 92px; }
  .website {
    position: absolute; left: 0; right: 0; top: 232px;
    text-align: center;
    font-size: 15px; letter-spacing: 1.5px;
    color: #d8d8d8;
  }

  .card--front .wordmark { left: 200px; top: 28px; }
  .tagline {
    position: absolute; left: 274px; top: 106px;
    font-size: 11px; letter-spacing: 3.2px;
    color: #d0d0d0; text-transform: uppercase;
  }
  .address {
    position: absolute; left: 200px; top: 128px;
    font-size: 13.5px; color: #ececec;
  }
  .wave { position: absolute; inset: 0; }
  .person { position: absolute; left: 26px; top: 186px; }
  .person__name { font-weight: 800; font-size: 19px; line-height: 1.3; color: var(--name-blue); }
  .person__role { font-size: 14px; line-height: 1.4; color: #e6f1fa; }

  .contacts {
    position: absolute; right: 26px; bottom: 20px;
    list-style: none;
    font-size: 15px; line-height: 1.55;
  }
  .contacts li { display: flex; align-items: center; gap: 8px; }
  .contacts svg { width: 15px; height: 15px; fill: var(--white); }
  .email {
    position: absolute; left: 160px; bottom: 62px;
    display: flex; align-items: center; gap: 8px;
    font-size: 15px;
  }
  .email svg { width: 16px; height: 13px; fill: var(--white); }
</style>
</head>
<body>
<main class="canvas">

  <section class="card card--back" aria-label="Card reverse">
    <div class="wordmark">
      <span class="wordmark__mark"></span>
      <span class="wordmark__name">Ridgeway<br>Networking</span>
    </div>
    <p class="website">www.ridgewaynet.com.au</p>
  </section>

  <section class="card card--front" aria-label="Card front">
    <svg class="wave" viewBox="0 0 580 331" preserveAspectRatio="none">
      <path d="M0 106 C120 116, 180 156, 260 206 C340 251, 470 216, 580 226 L580 331 L0 331 Z" fill="var(--blue)"/>
      <path d="M0 98 C120 108, 180 148, 260 198 C340 243, 470 208, 580 218" fill="none" stroke="var(--silver)" stroke-width="3"/>
      <path d="M0 90 C120 100, 180 140, 260 190 C340 235, 470 200, 580 210" fill="none" stroke="var(--blue-light)" stroke-width="4"/>
    </svg>

    <div class="wordmark">
      <span class="wordmark__mark"></span>
      <span class="wordmark__name">Ridgeway<br>Networking</span>
    </div>
    <p class="tagline">Complete IT Management</p>
    <p class="address">Unit 4 18 Coral Street, Westfield WA 6000</p>

    <div class="person">
      <p class="person__name">Marcus Hale</p>
      <p class="person__role">Operations Manager</p>
    </div>

    <p class="email">
      <svg viewBox="0 0 16 13"><path d="M0 0h16v13H0z M1.5 1.5 8 7l6.5-5.5v10h-13z" fill-rule="evenodd"/></svg>
      marcus@ridgewaynet.com.au
    </p>

    <ul class="contacts">
      <li><svg viewBox="0 0 16 16"><path d="M3 1l3 3-1.5 2a9 9 0 0 0 5.5 5.5L12 10l3 3-2 2C7 15 1 9 1 3z"/></svg>08 5550 1840</li>
      <li><svg viewBox="0 0 16 16"><path d="M4 0h8v16H4z M5.5 2v6h5V2z" fill-rule="evenodd"/></svg>0400 555 718</li>
      <li><svg viewBox="0 0 16 16"><path d="M4 0h8v5H4z M1 6h14v7H1z M4 11h8v5H4z"/></svg>08 5550 1840</li>
    </ul>
  </section>

</main>
</body>
</html>
```